Mortgage and Asset Finance Broker Needs a Wordpress Website Design

I need a modern looking Wordpress website to showcase my service as a mortgage and asset broker. I have a company and we work with various lenders to arrange mortgages, as well as commercial lending and business asset finance. The website needs to look professional, be easy to navigate and capture leads. SEO is obviously very important to me. It really needs to be something that shows trust and professioanlism.
Updates

On the home page I will need to have some boxes for Home Loans, Refinancing, Business (and Agriculture) Loans etc. I'd like a carousel in the middle which shows our lenders (so that can have the banks logos added).

It needs to be easy top navigate and showcase all we do - Home Loans, Refinancing, Commercial Loans, Car Loans, Asset Finance etc.

There are plenty of companies on the internet that do this.

There is some good information here https://lendplatehq.com.au/mortgage-broker-homepage/

I need to make sure that editing the website is easy (I think Wordpress has something that allows that).

Also we are very much an Australian business so that is something to advertise.

Industry/Entity Type

Mortgage and Finance Broker

Coding

Coded - Design and coding required

Number of Pages Required

5+ page

Requirements
Must have
• Easy to navigate professional feel. Must be responsive and mobile friendly.
Nice to have
• Homepage with links to inner pages. Contact buttons.

```html
<!DOCTYPE html>
<html lang="en">
<head>
<meta charset="utf-8">
<title>Northvale Financial Services – Mortgage &amp; Finance Brokers</title>
<link href="https://fonts.googleapis.com/css2?family=Poppins:wght@400;500;600&display=swap" rel="stylesheet">
<style>
:root{
  --blue:#1d5fae;
  --pink:#d6246e;
  --purple:#8a2f8f;
  --orange:#f29a1f;
  --ink:#1c1c1c;
  --muted:#555;
  --grey:#efedef;
  --white:#fff;
}
*{box-sizing:border-box;margin:0;padding:0}
html,body{width:1200px;height:4050px;overflow:hidden}
body{font-family:'Poppins',sans-serif;color:var(--ink);background:var(--white);position:relative}
.abs{position:absolute}
.btn{position:absolute;background:var(--pink);color:#fff;border-radius:8px;font-size:15px;display:flex;align-items:center;justify-content:center}

/* header */
.brand{left:110px;top:22px;display:flex;align-items:center;gap:10px}
.brand-mark{width:40px;height:40px;border-radius:50%;background:var(--pink)}
.brand-name{font-size:26px;font-weight:600;color:var(--blue);line-height:1}
.brand-sub{font-size:10px;color:var(--ink);letter-spacing:.5px;font-weight:500}
.call{right:138px;top:14px;font-size:17px;display:flex;align-items:center;gap:8px}
.nav{left:0;top:100px;width:1200px;height:39px;background:var(--blue);display:flex;align-items:center;color:#fff;font-size:15px}
.nav span{position:absolute;top:11px}
.nav .active{font-weight:600}
.nav .active::after{content:"";position:absolute;left:0;top:26px;width:44px;height:4px;background:var(--orange);border-radius:2px}

/* hero */
.hero{left:0;top:139px;width:1200px;height:508px;background:linear-gradient(90deg,#f5f0ea 0%,#efe5d8 45%,#d9c2a8 70%,#b69a86 100%)}
.hero-photo{left:560px;top:139px;width:640px;height:508px;background:linear-gradient(120deg,rgba(230,200,150,.6),rgba(180,120,110,.5) 60%,rgba(214,36,110,.55));clip-path:polygon(15% 0,100% 0,100% 100%,0 100%)}
.hero-title{left:111px;top:250px;width:640px;font-size:42px;font-weight:500;line-height:57px;color:var(--ink)}
.hero-text{left:111px;top:395px;width:560px;font-size:17px;line-height:26px;color:#333}

/* section heads */
.head{position:absolute;left:0;width:1200px;text-align:center}
.head h2{font-size:38px;font-weight:500}
.head p{font-size:17px;margin-top:14px;color:#333}
.head .rule{width:128px;height:2px;background:var(--purple);margin:22px auto 0}
.intro{position:absolute;left:230px;width:740px;text-align:center;font-size:16px;line-height:26px;color:#444}

/* services */
.arrow{position:absolute;width:42px;height:42px;border-radius:50%;border:2px solid var(--pink);display:flex;align-items:center;justify-content:center;color:var(--pink);font-size:18px}
.svc{position:absolute;top:991px;width:220px;height:319px;border-radius:10px;background:#f7f7f7;box-shadow:0 0 6px rgba(0,0,0,.12)}
.svc.on{background:var(--pink);color:#fff}
.svc .img{position:absolute;left:11px;top:16px;width:198px;height:156px;border-radius:6px}
.svc .ico{position:absolute;left:18px;top:152px;width:46px;height:46px;border-radius:50%;background:#fff;border:2px solid #eee;display:flex;align-items:center;justify-content:center}
.svc.on .ico{background:var(--orange);border-color:var(--orange)}
.svc h3{position:absolute;left:22px;top:220px;font-size:15px;font-weight:500}
.svc p{position:absolute;left:22px;top:252px;width:180px;font-size:11px;line-height:16px;color:#555}
.svc.on p{color:#fff}

/* about */
.about{left:0;top:1395px;width:1200px;height:625px;background:var(--grey)}
.about-title{left:114px;top:1468px;font-size:38px;font-weight:500}
.about-sub{left:114px;top:1528px;font-size:17px;color:#333}
.about-rule{left:114px;top:1574px;width:108px;height:2px;background:var(--purple)}
.about-text{left:114px;width:440px;font-size:16px;line-height:26px;color:#444}

/* why */
.why{position:absolute;top:2330px;width:360px;text-align:center}
.why .ring{width:152px;height:152px;border-radius:50%;background:#f7e6db;margin:0 auto;display:flex;align-items:center;justify-content:center}
.why .disc{width:120px;height:120px;border-radius:50%;background:linear-gradient(135deg,var(--pink),var(--purple));display:flex;align-items:center;justify-content:center}
.why h3{font-size:20px;font-weight:500;margin-top:22px}
.why p{font-size:14px;line-height:23px;color:#444;margin-top:14px}

/* lenders */
.lenders{left:115px;top:2693px;width:964px;height:322px;border-radius:40px;background:linear-gradient(110deg,#d92d73,#c81f66 60%,#e04a86)}
.lenders-title{left:148px;top:2725px;font-size:36px;font-weight:500;color:#fff}
.lenders-sub{left:148px;top:2785px;font-size:17px;color:#fff}
.lenders-rule{left:148px;top:2830px;width:130px;height:2px;background:#fff}
.lender{position:absolute;top:2878px;display:flex;align-items:center;gap:10px;color:#fff;font-size:28px;font-weight:600}
.lender i{width:34px;height:34px;border-radius:50%;background:#fff;display:block}
.dot{position:absolute;top:2958px;width:14px;height:14px;border-radius:50%;border:1.5px solid #fff}
.dot.on{background:#fff}

/* testimonials */
.testi-bg{left:0;top:3102px;width:1200px;height:610px;background:var(--grey)}
.tcard{position:absolute;top:3350px;width:218px;height:277px;background:#fff;box-shadow:0 0 6px rgba(0,0,0,.1);text-align:center}
.tcard .q{font-size:52px;line-height:52px;color:var(--purple);font-weight:600;margin-top:16px;height:40px}
.tcard .stars{color:var(--orange);font-size:15px;letter-spacing:1px;margin-top:6px}
.tcard p{font-size:11px;line-height:16px;color:#444;padding:0 22px;margin-top:14px}
.tcard .who{position:absolute;left:48px;top:218px;display:flex;align-items:center;gap:10px;text-align:left}
.tcard .av{width:38px;height:38px;border-radius:50%;background:var(--orange);color:var(--ink);font-weight:600;font-size:16px;display:flex;align-items:center;justify-content:center}
.tcard .nm{font-size:13px;font-weight:500}
.tcard .tm{font-size:10px;color:#777}

/* footer */
.footer{left:0;top:3712px;width:1200px;height:338px;background:var(--blue);color:#fff}
.foot-brand{left:108px;top:3762px;font-size:46px;font-weight:600;color:#fff;line-height:1}
.foot-brand small{display:block;font-size:13px;font-weight:500;margin-top:4px;letter-spacing:.5px}
.foot-text{left:108px;top:3868px;width:300px;font-size:15px;line-height:24px;color:#fff}
.fcol{color:#fff}
.fcol h4{font-size:22px;font-weight:600;margin-bottom:12px}
.fcol div{font-size:15px;line-height:26.5px;padding-left:32px;position:relative}
.fcol div::before{content:"»";position:absolute;left:2px;top:-2px;font-size:18px}
.social{display:flex;gap:6px}
.social i{width:22px;height:22px;border-radius:50%;border:1.5px solid #fff;display:block}
.copyline{left:0;top:3990px;width:1200px;border-top:1px solid rgba(255,255,255,.3);text-align:center;font-size:13px;padding-top:18px;color:#fff}
</style>
</head>
<body>

<!-- header -->
<div class="abs brand">
  <div class="brand-mark"></div>
  <div><div class="brand-name">Northvale</div><div class="brand-sub">FINANCIAL SERVICES</div></div>
</div>
<div class="abs call">
  <svg width="20" height="20" viewBox="0 0 24 24" fill="none" stroke="#1c1c1c" stroke-width="2"><path d="M5 3h4l2 5-2.5 1.5a11 11 0 0 0 6 6L16 13l5 2v4a2 2 0 0 1-2 2A16 16 0 0 1 3 5a2 2 0 0 1 2-2z"/></svg>
  Call +61 400 100 200
</div>
<div class="btn" style="left:817px;top:48px;width:270px;height:34px">Contact Us for Free Consultation</div>

<nav class="abs nav">
  <span class="active" style="left:170px">Home</span>
  <span style="left:266px">About Us</span>
  <span style="left:381px">Our Services</span>
  <span style="left:522px">Our Lenders</span>
  <span style="left:659px">Blog</span>
  <span style="left:742px">Testimonials</span>
  <span style="left:884px">Contact Us</span>
  <svg style="position:absolute;left:1014px;top:11px" width="16" height="16" viewBox="0 0 24 24" fill="none" stroke="#fff" stroke-width="3"><circle cx="10" cy="10" r="7"/><path d="M15 15l6 6"/></svg>
</nav>

<!-- hero -->
<section>
  <div class="abs hero"></div>
  <div class="abs hero-photo" role="img" aria-label="Smiling couple sitting on the floor making a roof shape with their arms"></div>
  <h1 class="abs hero-title">Your Trusted Australian Mortgage &amp; Finance Experts</h1>
  <p class="abs hero-text">Lorem ipsum dolor sit amet, consectetur adipiscing elit, sed do eiusmod tempor incididunt ut labore et dolore magna aliqua. Quis ipsum suspendisse ultrices gravida.</p>
  <div class="btn" style="left:111px;top:487px;width:228px;height:36px">Get Started with Your Loan</div>
</section>

<!-- services -->
<section>
  <div class="head" style="top:722px"><h2>Our Services</h2><p>Lorem ipsum dolor sit amet, consectetur adipiscing</p><div class="rule"></div></div>
  <p class="intro" style="top:873px">Lorem ipsum dolor sit amet, consectetur adipiscing elit, sed do eiusmod tempor incididunt ut labore et dolore magna aliqua. Quis ipsum suspendisse ultrices gravida. Risus commodo viverra maecenas accumsan lacus vel facilisis.</p>

  <div class="arrow" style="left:34px;top:1130px">&#8249;</div>
  <div class="arrow" style="left:1124px;top:1130px">&#8250;</div>

  <div class="svc" style="left:110px">
    <div class="img" role="img" aria-label="House keys with a small house keyring" style="background:linear-gradient(135deg,#6b4b3a,#c7b8a8)"></div>
    <div class="ico"><svg width="24" height="24" viewBox="0 0 24 24" fill="none" stroke="#333" stroke-width="1.6"><path d="M3 11l9-7 9 7M5 10v10h14V10"/></svg></div>
    <h3>Home Loan</h3><p>Lorem ipsum dolor sit amet, consectetur adipiscing elit, sed do eiusmod tempor</p>
  </div>
  <div class="svc on" style="left:363px">
    <div class="img" role="img" aria-label="Seedling growing from a stack of coins" style="background:linear-gradient(135deg,#2f5a23,#8bb34a 50%,#3a2a1a)"></div>
    <div class="ico"><svg width="24" height="24" viewBox="0 0 24 24" fill="none" stroke="#fff" stroke-width="1.6"><path d="M12 20V10M12 10c0-4 4-6 7-6 0 3-3 6-7 6zM12 13c0-3-3-5-6-5 0 3 2 5 6 5z"/></svg></div>
    <h3>Agriculture Loan</h3><p>Lorem ipsum dolor sit amet, consectetur adipiscing elit, sed do eiusmod tempor</p>
  </div>
  <div class="svc" style="left:616px">
    <div class="img" role="img" aria-label="Hands reviewing business documents with a calculator" style="background:linear-gradient(135deg,#3a3a3a,#d9d9d9)"></div>
    <div class="ico"><svg width="24" height="24" viewBox="0 0 24 24" fill="none" stroke="#333" stroke-width="1.6"><circle cx="12" cy="13" r="7"/><path d="M12 9v8M10 11h3a1.5 1.5 0 0 1 0 3h-2"/></svg></div>
    <h3>Business Loan</h3><p>Lorem ipsum dolor sit amet, consectetur adipiscing elit, sed do eiusmod tempor</p>
  </div>
  <div class="svc" style="left:869px">
    <div class="img" role="img" aria-label="Toy car and keys beside a loan contract" style="background:linear-gradient(135deg,#8a8a8a,#d63a2e 50%,#e6dcd0)"></div>
    <div class="ico"><svg width="24" height="24" viewBox="0 0 24 24" fill="none" stroke="#333" stroke-width="1.6"><path d="M3 15l2-6h14l2 6v3H3z"/><circle cx="7" cy="18" r="1.5"/><circle cx="17" cy="18" r="1.5"/></svg></div>
    <h3>Car Loan</h3><p>Lorem ipsum dolor sit amet, consectetur adipiscing elit, sed do eiusmod tempor</p>
  </div>
</section>

<!-- about -->
<section>
  <div class="abs about"></div>
  <h2 class="abs about-title">About Us</h2>
  <p class="abs about-sub">Lorem ipsum dolor sit amet, consectetur adipiscing</p>
  <div class="abs about-rule"></div>
  <p class="abs about-text" style="top:1616px">Lorem ipsum dolor sit amet, consectetur adipiscing elit, sed do eiusmod tempor incididunt ut labore et dolore magna aliqua. Quis ipsum suspendisse ultrices gravida. Risus commodo viverra maecenas accumsan lacus vel facilisis.</p>
  <p class="abs about-text" style="top:1754px">Sed ut perspiciatis unde omnis iste natus error sit voluptatem accusantium doloremque laudantium, totam rem aperiam, eaque ipsa quae ab illo inventore veritatis et quasi architecto beatae vitae dicta sunt explicabo nemo enim ipsam voluptatem</p>
  <div class="btn" style="left:114px;top:1900px;width:228px;height:36px">Get Started with Your Loan</div>

  <div class="abs" style="left:690px;top:1494px;width:2px;height:428px;background:var(--purple)"></div>
  <div class="abs" style="left:1050px;top:1494px;width:2px;height:428px;background:var(--pink)"></div>
  <div class="abs" style="left:656px;top:1533px;width:431px;height:2px;background:var(--blue)"></div>
  <div class="abs" style="left:656px;top:1879px;width:431px;height:2px;background:var(--orange)"></div>
  <div class="abs" role="img" aria-label="Two advisers smiling across a meeting table" style="left:708px;top:1556px;width:328px;height:305px;border-radius:8px;background:linear-gradient(135deg,#cfd6da,#8c9a8a 50%,#e4e6e4)"></div>
</section>

<!-- why choose us -->
<section>
  <div class="head" style="top:2094px"><h2>Why Choose Us</h2><p>Lorem ipsum dolor sit amet, consectetur adipiscing</p></div>
  <p class="intro" style="top:2242px">Lorem ipsum dolor sit amet, consectetur adipiscing elit, sed do<br>labore et dolore magna aliqua. Quis ipsum suspendisse ultrices gravida. Risus commodo</p>

  <div class="why" style="left:70px">
    <div class="ring"><div class="disc"><svg width="60" height="60" viewBox="0 0 48 48" fill="none" stroke="#fff" stroke-width="2"><rect x="8" y="8" width="24" height="30" rx="2"/><path d="M13 16h14M13 22h14M13 28h10M30 34l10-14"/></svg></div></div>
    <h3>Excepteur Sint Occae</h3><p>Lorem ipsum dolor sit<br>amet, consectetur adipiscing elit, sed do<br>eiusmod tempor incididunt ut</p>
  </div>
  <div class="why" style="left:420px">
    <div class="ring"><div class="disc"><svg width="60" height="60" viewBox="0 0 48 48" fill="none" stroke="#fff" stroke-width="2"><rect x="12" y="10" width="26" height="18" rx="2"/><circle cx="25" cy="19" r="4"/><path d="M6 36l8-6h10l8 4 8-4"/></svg></div></div>
    <h3>Excepteur Sint Occae</h3><p>Lorem ipsum dolor sit<br>amet, consectetur adipiscing elit, sed do<br>eiusmod tempor incididunt ut</p>
  </div>
  <div class="why" style="left:770px">
    <div class="ring"><div class="disc"><svg width="60" height="60" viewBox="0 0 48 48" fill="none" stroke="#fff" stroke-width="2"><circle cx="20" cy="20" r="9"/><path d="M16 24l8-8M16 16h.1M24 24h.1M26 32l6 4 10-8"/></svg></div></div>
    <h3>Excepteur Sint Occae</h3><p>Lorem ipsum dolor sit<br>amet, consectetur adipiscing elit, sed do<br>eiusmod tempor incididunt ut</p>
  </div>
</section>

<!-- lenders -->
<section>
  <div class="abs lenders" role="img" aria-label="Pink-tinted bank building columns in the background"></div>
  <h2 class="abs lenders-title">Our Lenders</h2>
  <p class="abs lenders-sub">Lorem ipsum dolor sit amet, consectetur adipiscing</p>
  <div class="abs lenders-rule"></div>
  <div class="lender" style="left:150px"><i></i>Lendora</div>
  <div class="lender" style="left:392px;font-weight:500;letter-spacing:2px">Southbank</div>
  <div class="lender" style="left:628px">Harbourline</div>
  <div class="lender" style="left:860px"><i></i>Coastal</div>
  <div class="dot" style="left:553px"></div>
  <div class="dot on" style="left:577px"></div>
  <div class="dot" style="left:600px"></div>
  <div class="dot" style="left:623px"></div>
</section>

<!-- testimonials -->
<section>
  <div class="abs testi-bg"></div>
  <div class="head" style="top:3177px"><h2>Client Testimonials</h2><p>Lorem ipsum dolor sit amet, consectetur adipiscing</p><div class="rule"></div></div>
  <div class="arrow" style="left:34px;top:3470px">&#8249;</div>
  <div class="arrow" style="left:1124px;top:3470px">&#8250;</div>

  <div class="tcard" style="left:111px"><div class="q">&ldquo;</div><div class="stars">★★★★☆</div><p>Lorem ipsum dolor sit amet, consectetur adipiscing elit, sed do eiusmod tempor incididunt ut labore et dolore magna aliqua. Quis ipsum suspendisse ultrices gravida.</p><div class="who"><div class="av">SC</div><div><div class="nm">Sam Carter</div><div class="tm">3 Mins</div></div></div></div>
  <div class="tcard" style="left:364px"><div class="q">&ldquo;</div><div class="stars">★★★★☆</div><p>Lorem ipsum dolor sit amet, consectetur adipiscing elit, sed do eiusmod tempor incididunt ut labore et dolore magna aliqua. Quis ipsum suspendisse ultrices gravida.</p><div class="who"><div class="av">SC</div><div><div class="nm">Sam Carter</div><div class="tm">3 Mins</div></div></div></div>
  <div class="tcard" style="left:616px"><div class="q">&ldquo;</div><div class="stars">★★★★☆</div><p>Lorem ipsum dolor sit amet, consectetur adipiscing elit, sed do eiusmod tempor incididunt ut labore et dolore magna aliqua. Quis ipsum suspendisse ultrices gravida.</p><div class="who"><div class="av">SC</div><div><div class="nm">Sam Carter</div><div class="tm">3 Mins</div></div></div></div>
  <div class="tcard" style="left:869px"><div class="q">&ldquo;</div><div class="stars">★★★★☆</div><p>Lorem ipsum dolor sit amet, consectetur adipiscing elit, sed do eiusmod tempor incididunt ut labore et dolore magna aliqua. Quis ipsum suspendisse ultrices gravida.</p><div class="who"><div class="av">SC</div><div><div class="nm">Sam Carter</div><div class="tm">3 Mins</div></div></div></div>
</section>

<!-- footer -->
<footer>
  <div class="abs footer"></div>
  <div class="abs foot-brand">Northvale<small>FINANCIAL SERVICES</small></div>
  <p class="abs foot-text">Sed ut perspiciatis unde omnis iste natus error sit voluptatem accusantium doloremque laudantium, totam rem aperiam, eaque ipsa quae</p>
  <div class="abs fcol" style="left:490px;top:3756px"><h4>Quick Links</h4><div>Home</div><div>About Us</div><div>Services</div><div>Testimonials</div><div>Blog</div><div>Contact Us</div></div>
  <div class="abs fcol" style="left:685px;top:3756px"><h4>Other Links</h4><div>FAQs</div><div>Help Center</div><div>Terms &amp; Conditions</div><div>Privacy Policy</div><div>Sitemap</div></div>
  <div class="abs fcol" style="left:925px;top:3756px"><h4>Follow Us</h4><span class="social"><i></i><i></i><i></i><i></i><i></i></span></div>
  <div class="abs copyline">Copyright © 2025 Northvale Financial Services All rights reserved.</div>
</footer>

</body>
</html>
```